Erotik Online Shop
Zielgruppe
Kunden des Online Shops, vorzugsweise schwule Männer wobei der Shop auch die hetero Ziegruppe bedienen bzw. befriedigen kann.
Aufgabenstellung
Für den Relounch unserers Online Shops benötigen wir mehrer Grafiken für die Startseite des Shops sowie eventuell einen Überabreitung unseres Logos.

```html
<!DOCTYPE html>
<html lang="de">
<head>
<meta charset="utf-8">
<title>Pluvo24 – Scharfmacher</title>
<link rel="stylesheet" href="https://fonts.googleapis.com/css2?family=Open+Sans:wght@300;400;600&display=swap">
<style>
  :root {
    --page: #ffffff;
    --bg-dark: #050505;
    --bg-mid: #1e1e1e;
    --bg-light: #5a5a5a;
    --accent: #e2423b;
    --text-light: #ffffff;
    --pepper-green: #5fae2e;
    --pepper-red: #d8231c;
    --flame: #f29a1c;
  }
  * { margin: 0; padding: 0; box-sizing: border-box; }
  html, body {
    width: 1200px;
    height: 688px;
    overflow: hidden;
    background: var(--page);
  }
  .banner {
    position: relative;
    width: 1200px;
    height: 688px;
    border-radius: 22px;
    overflow: hidden;
    background:
      radial-gradient(ellipse 900px 700px at 100% 0%, var(--bg-light) 0%, var(--bg-mid) 55%, var(--bg-dark) 100%);
    font-family: "Open Sans", "Segoe UI", sans-serif;
  }
  .headline {
    position: absolute;
    left: 74px;
    top: 54px;
    color: var(--accent);
    font-weight: 300;
    font-size: 58px;
    line-height: 88px;
    letter-spacing: -0.5px;
  }
  .subline {
    position: absolute;
    left: 78px;
    top: 270px;
    color: var(--text-light);
    font-weight: 300;
    font-size: 33px;
    line-height: 50px;
  }
  .product-visual {
    position: absolute;
    left: 285px;
    top: 74px;
    width: 810px;
    height: 590px;
  }
  .brand {
    position: absolute;
    right: 52px;
    bottom: 42px;
    color: var(--accent);
    font-weight: 600;
    font-size: 68px;
    line-height: 1;
    letter-spacing: -1px;
  }
</style>
</head>
<body>
  <main class="banner">
    <h1 class="headline">Sie mögen’s<br>gerne scharf?</h1>
    <p class="subline">Wir haben die<br>Scharfmacher.</p>

    <svg class="product-visual" viewBox="0 0 810 590" role="img"
         aria-label="Foto: grüne Peperoni liegt quer über einer roten Chilischote, aus der Flammen schlagen">
      <defs>
        <radialGradient id="pepperGlow" cx="50%" cy="55%" r="50%">
          <stop offset="0%" stop-color="var(--flame)" stop-opacity="0.55"/>
          <stop offset="35%" stop-color="var(--pepper-red)" stop-opacity="0.45"/>
          <stop offset="70%" stop-color="var(--pepper-green)" stop-opacity="0.35"/>
          <stop offset="100%" stop-color="var(--pepper-green)" stop-opacity="0"/>
        </radialGradient>
      </defs>
      <rect width="810" height="590" fill="url(#pepperGlow)"/>
    </svg>

    <div class="brand">Pluvo24</div>
  </main>
</body>
</html>
```